Brell Stone Company Business Cards

Front and Back Business Card - logo and text setup - cool design. I need workable photoshop or illustrator files so I can setup each employee card with design that is created
Updates

Hi everyone, thank you for the great entries. Please no more white and blue cards - there are so many already - black and silver only now please. thanks!

Target Market(s)

Construction Industry - Facility Managers

Industry/Entity Type

Construction

Contact Information for Business Card

I really like contemporary simplistic looks - clean neat....not opposed to seeing some black backrounds

Requirements
Must have
• Logo/website address with design on front only - www.brellstone-example.com (logo attached)
• Back:
• Name/Title/Company Address/Phone/email address
Nice to have
• Cool design
Should not have
• Nothing gimmicky like Fire or Water - since we are a Fire Protection company - it has all been done

```html
<!DOCTYPE html>
<html lang="en">
<head>
<meta charset="utf-8">
<title>Brell Stone Company — Business Cards</title>
<link rel="stylesheet" href="https://fonts.googleapis.com/css2?family=Lato:wght@300;400&family=Oswald:wght@500&display=swap">
<style>
  :root {
    --backdrop: #1b1b1d;
    --card: #252526;
    --card-edge: #2c2c2d;
    --silver: #c9c9cb;
    --text-light: #c8c8ca;
    --text-muted: #9a9a9c;
    --accent-blue: #34427a;
    --divider: #6a6a6c;
  }
  * { margin: 0; padding: 0; box-sizing: border-box; }
  html, body {
    width: 1200px;
    height: 912px;
    overflow: hidden;
    background: var(--backdrop);
  }
  .canvas {
    position: relative;
    width: 1200px;
    height: 912px;
  }
  .card {
    position: absolute;
    width: 560px;
    height: 320px;
    background: linear-gradient(160deg, var(--card-edge), var(--card));
    box-shadow: 0 18px 40px rgba(0,0,0,0.55);
    overflow: hidden;
  }

  /* Front */
  .card-front { left: 70px; top: 90px; }
  .brand {
    position: absolute;
    left: 0; right: 0; top: 110px;
    display: flex;
    align-items: center;
    justify-content: center;
    gap: 16px;
  }
  .brand-mark {
    width: 22px; height: 22px;
    background: var(--silver);
  }
  .brand-name {
    font-family: "Lato", sans-serif;
    font-weight: 400;
    font-size: 52px;
    letter-spacing: 1px;
    color: var(--silver);
  }
  .front-web {
    position: absolute;
    left: 0; right: 0; top: 214px;
    text-align: center;
    font-family: "Lato", sans-serif;
    font-weight: 400;
    font-size: 15px;
    letter-spacing: 0.5px;
    color: var(--text-muted);
  }

  /* Back */
  .card-back { left: 570px; top: 500px; }
  .accent-band {
    position: absolute;
    left: 0; right: 0; bottom: 0;
    height: 6px;
    background: var(--accent-blue);
  }
  .identity {
    position: absolute;
    right: 300px;
    top: 118px;
    text-align: right;
  }
  .person-name {
    font-family: "Oswald", sans-serif;
    font-weight: 500;
    font-size: 25px;
    letter-spacing: -0.3px;
    text-transform: uppercase;
    color: var(--accent-blue);
    line-height: 1.1;
  }
  .person-title {
    font-family: "Lato", sans-serif;
    font-weight: 400;
    font-size: 16px;
    color: var(--text-light);
    margin-top: 4px;
  }
  .divider {
    position: absolute;
    left: 280px;
    top: 86px;
    width: 1px;
    height: 118px;
    background: var(--divider);
  }
  .contact {
    position: absolute;
    left: 302px;
    top: 84px;
    font-family: "Lato", sans-serif;
    font-weight: 300;
    font-size: 13.5px;
    color: var(--text-light);
    line-height: 1.4;
  }
  .address { margin-bottom: 12px; }
  .contact-list { list-style: none; }
  .contact-list li {
    display: flex;
    align-items: center;
    gap: 9px;
  }
  .contact-list svg {
    width: 11px; height: 11px;
    flex: none;
    fill: var(--accent-blue);
  }
</style>
</head>
<body>
<div class="canvas">

  <section class="card card-front" aria-label="Business card front">
    <div class="brand">
      <span class="brand-mark"></span>
      <span class="brand-name">Brell Stone</span>
    </div>
    <p class="front-web">www.brellstone-example.com</p>
  </section>

  <section class="card card-back" aria-label="Business card back">
    <div class="identity">
      <p class="person-name">Dana Ellery Marsh</p>
      <p class="person-title">President</p>
    </div>
    <span class="divider"></span>
    <div class="contact">
      <p class="address">48 Harbor Works Lane<br>Millbrook, NY 10000</p>
      <ul class="contact-list">
        <li>
          <svg viewBox="0 0 12 12" aria-hidden="true"><path d="M2.4 0.8 L4.2 2.9 L3.3 4.2 Q4.3 6.6 7.6 8.7 L8.9 7.8 L11.2 9.6 L10.1 11.3 Q4.8 11 0.8 2.1 Z"/></svg>
          <span>(555) 014-2290</span>
        </li>
        <li>
          <svg viewBox="0 0 12 12" aria-hidden="true"><path d="M0.5 2.5 H11.5 V9.5 H0.5 Z M1.2 3 L6 6.6 L10.8 3 Z" fill-rule="evenodd"/></svg>
          <span>info@brellstone-example.com</span>
        </li>
        <li>
          <svg viewBox="0 0 12 12" aria-hidden="true"><circle cx="6" cy="6" r="5.5"/><path d="M0.5 6 H11.5 M6 0.5 V11.5 M1.5 3.5 H10.5 M1.5 8.5 H10.5" stroke="#252526" stroke-width="0.8" fill="none"/></svg>
          <span>www.brellstone-example.com</span>
        </li>
      </ul>
    </div>
    <span class="accent-band"></span>
  </section>

</div>
</body>
</html>
```